Classy, Elegant, Simple Business Card Design

Looking to have a classy, simple, and elegant design. Want a top notch designed business card. I really like the look of the new torvane credit card. I also like the design I attached. I am trying to reach 21-29 year old females for booking us for there wedding or event. We offer Disc Jockey Service, Photo Booth Rentals, and Uplighting .

Target Market(s)

21-28 year old females

Contact Information for Business Card

Has to have logo, website, email, and phone number

Font styles to use
Other font styles liked:
• open to font choice, modern, clean
Designer to choose
33a6d7
0791cd
0555a3
ffffff

Requirements
Must have
• Has to have logo, website, email, and phone number
Nice to have
• I really like the design of the new torvane credit card. I also included my logo and some designs I like
Should not have
• clutter or too much info

```html
<!DOCTYPE html>
<html lang="en">
<head>
<meta charset="utf-8">
<title>Tidecrest Event Group – Business Card</title>
<link rel="stylesheet" href="https://fonts.googleapis.com/css2?family=Jost:wght@300;400;600&family=Arimo:wght@400;700&display=swap">
<style>
  :root {
    --backdrop: #2c2c2e;
    --card: #1d1d1f;
    --card-edge: #151516;
    --silver: #9a9a9e;
    --silver-soft: #6e6e72;
    --white: #ffffff;
    --blue: #0791cd;
    --blue-light: #33a6d7;
    --blue-deep: #0555a3;
    --ray: #2a2a2d;
  }
  * { box-sizing: border-box; margin: 0; padding: 0; }
  html, body { width: 799px; height: 1200px; overflow: hidden; }
  body {
    background: var(--backdrop);
    position: relative;
    font-family: "Jost", sans-serif;
  }
  .card {
    position: absolute;
    left: 90px;
    width: 620px;
    height: 354px;
    background: var(--card);
    border: 1px solid var(--card-edge);
    border-radius: 4px;
    box-shadow: 0 18px 40px rgba(0,0,0,0.45);
    overflow: hidden;
  }
  .card--front { top: 160px; }
  .card--back { top: 690px; }

  /* Front */
  .front-brand {
    position: absolute;
    left: 0; right: 0; top: 0; bottom: 0;
    display: flex;
    flex-direction: column;
    align-items: center;
    justify-content: center;
    gap: 14px;
  }
  .front-brand__dot {
    width: 74px; height: 74px;
    border-radius: 50%;
    border: 2px solid var(--silver-soft);
  }
  .front-brand__name {
    font-family: "Jost", sans-serif;
    font-weight: 400;
    font-size: 40px;
    letter-spacing: 3px;
    color: var(--silver);
    text-transform: uppercase;
    line-height: 1;
    text-align: center;
  }
  .front-brand__name span { display: block; font-size: 17px; letter-spacing: 9px; margin-top: 8px; }

  /* Back */
  .burst {
    position: absolute;
    left: 22px; top: 32px;
    width: 290px; height: 290px;
    border-radius: 50%;
    background: radial-gradient(circle, #1d1d1f 0 54%, var(--ray) 55% 62%, #232326 63% 100%);
  }
  .burst__mark {
    position: absolute;
    left: 50%; top: 50%;
    width: 120px; height: 120px;
    transform: translate(-50%, -50%);
    border-radius: 50%;
    border: 3px solid var(--blue);
  }
  .details {
    position: absolute;
    left: 340px; top: 62px;
    width: 260px;
    color: var(--white);
  }
  .details__brand {
    font-family: "Jost", sans-serif;
    font-weight: 400;
    font-size: 26px;
    letter-spacing: 1.5px;
    text-transform: uppercase;
    line-height: 1;
    color: var(--white);
    text-align: center;
  }
  .details__brand span { display: block; font-size: 11px; letter-spacing: 6px; margin-top: 4px; }
  .details__name {
    margin-top: 26px;
    font-family: "Arimo", sans-serif;
    font-weight: 700;
    font-size: 22px;
    color: var(--blue);
  }
  .details__role {
    font-family: "Arimo", sans-serif;
    font-size: 14px;
    margin-top: 2px;
  }
  .contact { list-style: none; margin-top: 16px; font-family: "Arimo", sans-serif; font-size: 15px; }
  .contact li { display: flex; align-items: center; gap: 10px; margin-bottom: 6px; }
  .contact svg { width: 13px; height: 13px; flex: none; }
  .contact .no-icon { padding-left: 23px; }
</style>
</head>
<body>
  <section class="card card--front" aria-label="Card front">
    <div class="front-brand">
      <div class="front-brand__dot"></div>
      <p class="front-brand__name">Tidecrest<span>Event Group</span></p>
    </div>
  </section>

  <section class="card card--back" aria-label="Card back">
    <div class="burst" role="img" aria-label="Radial sound-burst decoration around the brand mark">
      <div class="burst__mark"></div>
    </div>
    <div class="details">
      <p class="details__brand">Tidecrest<span>Event Group</span></p>
      <p class="details__name">Mara Ellison</p>
      <p class="details__role">Founder &amp; CEO</p>
      <ul class="contact">
        <li>
          <svg viewBox="0 0 16 16" aria-hidden="true"><path fill="var(--blue)" d="M4 1l3 3-2 2c1 2 3 4 5 5l2-2 3 3-2 3C7 15 1 9 1 3z"/></svg>
          555 0142 0199
        </li>
        <li>
          <svg viewBox="0 0 16 16" aria-hidden="true"><rect x="1" y="3" width="14" height="10" fill="var(--blue)"/><path d="M1 3l7 6 7-6" stroke="#1d1d1f" stroke-width="1.5" fill="none"/></svg>
          mara@tidecrest.com
        </li>
        <li>
          <svg viewBox="0 0 16 16" aria-hidden="true"><circle cx="8" cy="8" r="7" fill="var(--blue)"/><path d="M1 8h14M8 1c-3 4-3 10 0 14M8 1c3 4 3 10 0 14" stroke="#1d1d1f" stroke-width="1" fill="none"/></svg>
          www.tidecrest.com
        </li>
      </ul>
    </div>
  </section>
</body>
</html>
```